I need a business card for my original fine art pieces

I would like a business card design including a logo design for a new business in the art world. I am based in the Hunter Valley NSW Australia. I am a contemporary figurative, encaustic and wildlife artist. I would like to be able to upload my email and mobile number to this as well. This design should be one that I can incorporate into banners and flyers etc. Id like to incorporate one of my own images or partial image into the background or somewhere below. My initials are RJ and I would like these used as a logo type. I would like the use of some colour and it to be bright and catchy. The final design should communicate artwork custom made and commissions available.

Overview: Original Fine Artworks for sale, online, art galleries etc, Custom made to order and by commission.

Target market is world wide audience and corporate world

My figurative work is painted using acrylics in a lot of natural ochre colours that reflect the Australian Outback, on canvas, linen, paper or board: My encaustic work is created in a contemporary abstract style using a blow torch and a made with a medium of 100% pure bees wax, Damar resin, mixed media and coloured pigments, applied to Birch board. My wildlife are created using coloured pencil and mixed media on a variety of paper types or board.

```html
<!DOCTYPE html>
<html lang="en">
<head>
<meta charset="utf-8">
<title>Rhea Jarvis – Business Card</title>
<link rel="stylesheet" href="https://fonts.googleapis.com/css2?family=Cinzel:wght@500&family=Lato:wght@400;700&family=Lora:wght@500&display=swap">
<style>
  :root {
    --bg: #2b2b2b;
    --card: #ffffff;
    --ink: #1b1b1b;
    --black: #050505;
    --accent: #ef4e23;
    --muted: #e9e9e9;
    --sketch-light: #f2f2f2;
    --sketch-dark: #6f6f6f;
  }
  * { box-sizing: border-box; margin: 0; padding: 0; }
  html, body { width: 1200px; height: 900px; overflow: hidden; }
  body {
    background: var(--bg);
    position: relative;
    font-family: "Lato", Arial, sans-serif;
    color: var(--ink);
  }
  .card {
    position: absolute;
    width: 640px;
    height: 366px;
    background: var(--card);
    border-radius: 18px;
    overflow: hidden;
  }
  .card--front { left: 110px; top: 70px; }
  .card--back { left: 450px; top: 470px; }

  /* brand block */
  .brand { position: absolute; text-align: center; }
  .brand__circle {
    display: block;
    margin: 0 auto;
    border: 4px solid var(--accent);
    border-radius: 50%;
  }
  .brand__name {
    font-family: "Cinzel", Georgia, serif;
    font-weight: 500;
    color: var(--accent);
    letter-spacing: 1px;
    line-height: 1;
    white-space: nowrap;
  }
  .brand__tagline {
    font-family: "Lato", Arial, sans-serif;
    letter-spacing: 4px;
    color: var(--ink);
    white-space: nowrap;
  }

  /* front */
  .card--front .brand { left: 40px; top: 42px; width: 330px; }
  .card--front .brand__circle { width: 112px; height: 112px; }
  .card--front .brand__name { font-size: 36px; margin-top: 16px; }
  .card--front .brand__tagline { font-size: 15px; margin-top: 4px; }
  .offer {
    margin-top: 12px;
    font-size: 15px;
    line-height: 1.35;
    color: var(--ink);
  }
  .artwork {
    position: absolute;
    right: 0; top: 0;
    width: 260px; height: 366px;
    background: linear-gradient(160deg, var(--sketch-light) 0%, #d6d6d6 45%, var(--sketch-dark) 100%);
  }

  /* back */
  .back-shape { position: absolute; inset: 0; }
  .contact {
    position: absolute;
    left: 50px; top: 120px;
    color: #fff;
  }
  .contact__name {
    font-family: "Lora", Georgia, serif;
    font-weight: 500;
    font-size: 30px;
    color: var(--accent);
    line-height: 1;
  }
  .contact__role { font-size: 16px; margin-top: 4px; }
  .contact__meta { font-size: 16px; line-height: 1.3; margin-top: 16px; }
  .contact__list { list-style: none; margin-top: 14px; font-size: 16px; }
  .contact__list li { display: flex; align-items: center; gap: 10px; line-height: 1.45; }
  .contact__list svg { width: 14px; height: 14px; flex: none; }
  .contact__highlight { color: var(--accent); font-weight: 700; }

  .card--back .brand { left: 370px; top: 52px; width: 250px; }
  .card--back .brand__circle { width: 100px; height: 100px; }
  .card--back .brand__name { font-size: 31px; margin-top: 16px; }
  .card--back .brand__tagline { font-size: 13px; margin-top: 4px; letter-spacing: 3px; }
</style>
</head>
<body>

  <section class="card card--front" aria-label="Card front">
    <div class="brand">
      <span class="brand__circle" aria-hidden="true"></span>
      <p class="brand__name">Rhea Jarvis</p>
      <p class="brand__tagline">ORIGINAL FINE ARTWORKS</p>
      <p class="offer">
        Original Fine Artworks for sale<br>
        online, art galleries etc<br>
        Custom made to order and by commission.
      </p>
    </div>
    <div class="artwork" role="img" aria-label="Ink sketch of an elegant figure in an evening gown"></div>
  </section>

  <section class="card card--back" aria-label="Card back">
    <svg class="back-shape" viewBox="0 0 640 366" preserveAspectRatio="none" aria-hidden="true">
      <path d="M0,70 C140,10 330,40 345,190 C352,270 310,330 270,366 L0,366 Z" fill="var(--black)"/>
      <path d="M90,32 C270,8 380,110 366,225 C358,290 320,340 292,366" fill="none" stroke="var(--accent)" stroke-width="6"/>
    </svg>

    <div class="contact">
      <p class="contact__name">Rhea Jarvis</p>
      <p class="contact__role">Director</p>
      <p class="contact__meta">Cessnock Australia<br>ABN 12 345 678 901</p>
      <ul class="contact__list">
        <li>
          <svg viewBox="0 0 14 14"><rect x="3" y="1" width="8" height="12" rx="1.5" fill="none" stroke="var(--accent)" stroke-width="1.6"/><circle cx="7" cy="10.5" r="0.9" fill="var(--accent)"/></svg>
          +61 400 123 456
        </li>
        <li>
          <svg viewBox="0 0 14 14"><rect x="1" y="3" width="12" height="8" fill="none" stroke="var(--accent)" stroke-width="1.6"/><path d="M1,3 L7,8 L13,3" fill="none" stroke="var(--accent)" stroke-width="1.4"/></svg>
          rhea@jarvisart.com
        </li>
        <li>
          <svg viewBox="0 0 14 14"><circle cx="7" cy="7" r="6" fill="var(--accent)"/><path d="M1,7 H13 M7,1 C4,4 4,10 7,13 M7,1 C10,4 10,10 7,13" fill="none" stroke="var(--black)" stroke-width="0.9"/></svg>
          <span>www.<span class="contact__highlight">rheajarvis</span>.com</span>
        </li>
      </ul>
    </div>

    <div class="brand">
      <span class="brand__circle" aria-hidden="true"></span>
      <p class="brand__name">Rhea Jarvis</p>
      <p class="brand__tagline">ORIGINAL FINE ARTWORKS</p>
    </div>
  </section>

</body>
</html>
```